Website for Excavator and Earthworks Company

We require a modern, sleek and practical website for our newly created earthworks/excavator business in Perth, Western Australia called Bluegum Ridge Earthworks.

The website should have a modern, cutting edge feel but only needs to be relatively simplistic in it's layout and eventual functionality.

Some pages it should have would be Home, About, Projects and Contact Us.

```html
<!DOCTYPE html>
<html lang="en">
<head>
<meta charset="utf-8">
<title>Bluegum Ridge Earthworks</title>
<link href="https://fonts.googleapis.com/css2?family=Roboto:wght@400;500;700;900&family=Poppins:wght@400;500;600&display=swap" rel="stylesheet">
<style>
:root{
  --lime:#cddc00;
  --ink:#111;
  --dark:#1f1f1f;
  --grey:#ececec;
  --light:#f7f7f7;
  --white:#fff;
  --muted:#444;
}
*{box-sizing:border-box;margin:0;padding:0}
html,body{width:1200px;height:4491px;overflow:hidden}
body{position:relative;font-family:"Roboto",sans-serif;color:var(--ink);background:var(--white)}
section,header,footer{position:absolute;left:0;width:1200px}
.abs{position:absolute}
h1,h2{font-family:"Roboto",sans-serif;font-weight:900;text-transform:uppercase;line-height:1.05}
.btn{display:inline-flex;align-items:center;gap:6px;background:var(--lime);color:var(--ink);font-weight:700;font-size:12px;text-transform:uppercase;padding:9px 22px;border-radius:5px}
.btn svg{width:13px;height:13px}

/* header */
.site-header{top:0;height:75px;background:var(--lime)}
.brand-panel{position:absolute;left:0;top:0}
.brand{position:absolute;left:48px;top:18px;display:flex;align-items:center;gap:8px;font-family:"Poppins",sans-serif;font-weight:600;font-size:15px;color:var(--ink)}
.brand i{width:14px;height:14px;background:var(--lime);display:block}
.nav{position:absolute;right:60px;top:24px;display:flex;gap:0;font-weight:700;font-size:20px;text-transform:uppercase}
.nav a{color:var(--ink);text-decoration:none;padding:0 17px;border-left:2px solid var(--ink);line-height:1}
.nav a:first-child{border-left:0;color:var(--white)}

/* hero */
.hero{top:75px;height:684px;background:linear-gradient(180deg,#3f6fa8 0%,#7d9bbd 35%,#6b7a4e 62%,#6f8a3e 100%)}
.hero-shade{position:absolute;inset:0;background:rgba(0,0,0,.28)}
.hero-copy{position:absolute;left:0;width:1200px;top:205px;text-align:center;color:var(--white)}
.hero-copy h1{font-size:50px;letter-spacing:.5px}
.hero-copy p{width:1080px;margin:22px auto 0;font-size:13px;line-height:1.6}
.hero-copy .btn{margin-top:32px}
.arrow{position:absolute;top:313px;width:46px;height:46px;background:var(--lime);display:flex;align-items:center;justify-content:center}
.dots{position:absolute;top:768px;left:570px;display:flex;gap:11px}
.dots span{width:10px;height:10px;border-radius:50%;background:#bbb}
.dots span:first-child{background:#111}

/* about */
.about{top:759px;height:697px;background:var(--grey)}
.about h2{position:absolute;left:42px;top:226px;font-size:38px}
.about p{position:absolute;left:42px;top:325px;width:516px;font-size:13px;line-height:1.6;text-align:justify;color:#222}
.about .btn{position:absolute;left:42px;top:456px}
.ph{border-radius:8px}
.exp{position:absolute;left:607px;top:453px;width:168px;height:168px;border-radius:50%;background:var(--white);text-align:center;padding-top:38px}
.exp b{display:block;font-family:"Poppins",sans-serif;font-weight:600;font-size:54px;color:var(--lime);line-height:1}
.exp small{display:block;margin-top:10px;font-size:11px;font-weight:700;text-transform:uppercase;color:#333}

/* services */
.services{top:1456px;height:480px;background:var(--light)}
.services h2{position:absolute;top:62px;width:1200px;text-align:center;font-size:38px}
.card{position:absolute;top:131px;width:262px;height:267px;background:var(--white);border:2px solid #333;border-radius:8px;box-shadow:3px 3px 6px rgba(0,0,0,.35);padding:20px 14px}
.card svg{width:42px;height:42px}
.card h3{font-family:"Poppins",sans-serif;font-weight:500;font-size:17px;line-height:1.25;margin-top:12px}
.card p{font-size:12.5px;line-height:1.6;margin-top:14px;color:#222}

/* cta band */
.cta{top:1936px;height:549px;background:#2b2b2b}
.cta-bg{position:absolute;inset:0;background:linear-gradient(180deg,#3a3a3a,#252525)}
.cta h2{position:absolute;top:195px;width:1200px;text-align:center;color:var(--white);font-size:44px}
.cta .btn{position:absolute;left:515px;top:345px}
.lower-grey{top:2485px;height:881px;background:var(--grey)}
.excavator{position:absolute;top:1990px;width:400px;height:600px;border-radius:40% 40% 30% 30%}

/* projects */
.projects h2{position:absolute;top:200px;width:1200px;text-align:center;font-size:38px}
.project{position:absolute;top:265px;width:354px;height:540px;border-radius:12px;overflow:hidden;border:3px solid var(--lime);background:var(--lime);text-align:center}
.project.dark{background:#0c0c0c;border-color:#444;color:var(--white)}
.project .photo{height:318px;border-radius:0 0 50% 50% / 0 0 38% 38%}
.project h3{font-family:"Poppins",sans-serif;font-weight:500;font-size:17px;margin-top:36px}
.project.dark h3{color:var(--lime)}
.project p{font-size:12.5px;line-height:1.6;margin:16px 10px 0}

/* quote */
.quote{top:3366px;height:645px;background:var(--white)}
.quote h2{position:absolute;top:62px;width:1200px;text-align:center;font-size:38px}
.quote .lead{position:absolute;top:131px;width:1200px;text-align:center;font-size:13px;line-height:1.6}
.form{position:absolute;left:612px;top:227px;width:538px;height:319px;border:2px solid #333;border-radius:8px;padding:18px 22px}
.form label{position:absolute;font-size:12px;font-weight:700;text-transform:uppercase}
.form .field{position:absolute;height:32px;border:1px solid #999;border-radius:2px;font-size:11px;color:#aaa;padding:9px 12px}
.form .send{position:absolute;left:22px;top:270px;width:492px;height:32px;background:var(--lime);font-size:12px;font-weight:700;text-transform:uppercase;display:flex;align-items:center;justify-content:center}

/* footer */
.site-footer{top:4011px;height:480px;background:linear-gradient(180deg,#2a2724,#1a1816);color:var(--white);font-family:"Poppins",sans-serif}
.foot-brand{position:absolute;left:54px;top:116px;font-weight:600;font-size:20px;display:flex;align-items:center;gap:9px}
.foot-brand i{width:14px;height:14px;background:var(--lime);display:block}
.foot-about{position:absolute;left:54px;top:186px;width:270px;font-size:14px;line-height:1.55}
.social{position:absolute;left:54px;top:305px;display:flex;gap:16px}
.social span{width:28px;height:28px;border-radius:50%;background:var(--lime)}
.col{position:absolute;top:78px}
.col h4{color:var(--lime);font-weight:500;font-size:20px;margin-bottom:14px}
.col li{list-style:none;font-size:14px;line-height:1.15;margin-bottom:14px;display:flex;gap:9px;align-items:flex-start}
.col li::before{content:"";flex:0 0 10px;height:10px;margin-top:4px;border-radius:50%;border:3px solid var(--lime)}
.col.contact li::before{display:none}
.col.contact svg{flex:0 0 13px;height:13px;margin-top:3px}
.copyright{position:absolute;top:366px;width:1200px;text-align:center;font-size:14px}
</style>
</head>
<body>

<header class="site-header">
  <svg class="brand-panel" width="320" height="75" viewBox="0 0 320 75"><polygon points="0,0 314,0 204,75 0,75" fill="#fff"/></svg>
  <div class="brand"><i></i>Bluegum Ridge</div>
  <nav class="nav"><a>Home</a><a>About</a><a>Services</a><a>Projects</a><a>Contact</a></nav>
</header>

<section class="hero">
  <div class="abs" style="inset:0" role="img" aria-label="Yellow mini excavator on a grassy site under a blue sky"></div>
  <div class="hero-shade"></div>
  <div class="hero-copy">
    <h1>Professional Earthworks &amp; Excavation<br>Services in Perth, WA</h1>
    <p>Bluegum Ridge Earthworks is a Perth-based excavator and earthmoving business delivering dependable, high-quality earthworks across Western Australia. From residential site preparation to commercial excavation projects, we bring precision, safety, and efficiency to every job. With modern machinery, experienced operators, and a strong understanding of local soil and site conditions, we help projects get off the ground the right way — on time and on budget.</p>
    <span class="btn">Contact us now <svg viewBox="0 0 16 16"><circle cx="8" cy="8" r="7" fill="none" stroke="#111" stroke-width="1.6"/><path d="M5 8h6M8.5 5.5 11 8l-2.5 2.5" fill="none" stroke="#111" stroke-width="1.6"/></svg></span>
  </div>
  <div class="arrow" style="left:0"><svg width="16" height="16" viewBox="0 0 16 16"><path d="M10 3 5 8l5 5" fill="none" stroke="#111" stroke-width="2.2"/></svg></div>
  <div class="arrow" style="right:0"><svg width="16" height="16" viewBox="0 0 16 16"><path d="M6 3l5 5-5 5" fill="none" stroke="#111" stroke-width="2.2"/></svg></div>
</section>
<div class="dots"><span></span><span></span><span></span></div>

<section class="about" style="height:697px">
  <h2>About Bluegum Ridge<br>Earthworks</h2>
  <p>At <b>Bluegum Ridge Earthworks</b>, we deliver reliable, precision-driven earthmoving and excavation services across <b>Perth and Western Australia</b>. Whether you're preparing a residential block, managing a commercial build, or tackling a rural project, our experienced operators and modern machinery get the job done safely, efficiently, and on schedule.</p>
  <span class="btn">Know more about us <svg viewBox="0 0 16 16"><circle cx="8" cy="8" r="7" fill="none" stroke="#111" stroke-width="1.6"/><path d="M5 8h6M8.5 5.5 11 8l-2.5 2.5" fill="none" stroke="#111" stroke-width="1.6"/></svg></span>
  <div class="abs ph" style="left:636px;top:108px;width:349px;height:392px;background:linear-gradient(180deg,#dcd4c6,#b9a98f 55%,#8a7b64)" role="img" aria-label="Excavator on a rocky site with a worker in hi-vis reviewing plans"></div>
  <div class="abs ph" style="left:893px;top:178px;width:228px;height:261px;background:linear-gradient(180deg,#c9c7cf,#b88d7a 50%,#9a6250);border:3px solid #fff" role="img" aria-label="Excavator loading a dump truck in a red-earth quarry"></div>
  <div class="exp"><b>15+</b><small>Years of experience</small></div>
</section>

<section class="services">
  <h2>Our Earthworks &amp; Excavation Services</h2>
  <div class="card" style="left:52px">
    <svg viewBox="0 0 40 40"><rect x="4" y="26" width="30" height="8" rx="3" fill="#cddc00"/><rect x="10" y="16" width="14" height="10" fill="#cddc00"/><path d="M24 18 32 6l5 10" fill="none" stroke="#cddc00" stroke-width="3"/></svg>
    <h3>Excavation Services</h3>
    <p>We provide accurate and efficient excavation for projects of all sizes, including site cuts, footings, trenches, and foundations. Our attention to detail ensures your site is properly prepared from day one..</p>
  </div>
  <div class="card" style="left:331px">
    <svg viewBox="0 0 40 40"><rect x="4" y="30" width="32" height="5" fill="#cddc00"/><rect x="8" y="18" width="16" height="10" fill="#cddc00"/><path d="M24 20l10-10" stroke="#cddc00" stroke-width="3"/><circle cx="34" cy="8" r="4" fill="#cddc00"/></svg>
    <h3>Site Preparation &amp;<br>Levelling</h3>
    <p>Proper site preparation is critical. We handle clearing, levelling, and ground preparation to create a stable base for construction, landscaping, or infrastructure projects.</p>
  </div>
  <div class="card" style="left:610px">
    <svg viewBox="0 0 40 40"><rect x="4" y="24" width="26" height="10" rx="2" fill="#cddc00"/><path d="M12 24V12h14l6 12" fill="none" stroke="#cddc00" stroke-width="3"/></svg>
    <h3>Land Clearing &amp;<br>Earthworks</h3>
    <p>We provide accurate and efficient excavation for projects of all sizes, including site cuts, footings, trenches, and foundations. Our attention to detail ensures your site is properly prepared from day one.</p>
  </div>
  <div class="card" style="left:889px">
    <svg viewBox="0 0 40 40"><path d="M6 34h28l-6-12H12z" fill="#cddc00"/><path d="M14 22 20 8l8 8" fill="none" stroke="#cddc00" stroke-width="3"/></svg>
    <h3>Trenching &amp; Footings</h3>
    <p>Accurate trenching for plumbing, electrical, and foundation work. We ensure correct depths, clean lines, and compliance with Australian standards to support long-lasting, structurally sound builds.</p>
  </div>
</section>

<section class="cta">
  <div class="cta-bg" role="img" aria-label="Dim construction site with earthmoving machinery"></div>
  <h2>Fast, Reliable<br>Excavation Services<br>Across Perth, WA.</h2>
  <span class="btn">Get a free quote <svg viewBox="0 0 16 16"><circle cx="8" cy="8" r="7" fill="none" stroke="#111" stroke-width="1.6"/><path d="M5 8h6M8.5 5.5 11 8l-2.5 2.5" fill="none" stroke="#111" stroke-width="1.6"/></svg></span>
</section>

<section class="lower-grey projects" style="top:2485px">
  <h2 style="top:200px">Our Projects</h2>
  <div class="project" style="left:52px;top:265px">
    <div class="photo" style="background:linear-gradient(180deg,#6fa6d8,#c7a25a 70%,#a9773c)" role="img" aria-label="Yellow excavator digging sand"></div>
    <h3>Project Name Here</h3>
    <p>Lorem ipsum dolor sit amet, consectetur adipiscing elit, sed do eiusmod tempor incididunt ut labore et dolore magna aliqua. Vulputate dignissim suspendisse in est ante.</p>
  </div>
  <div class="project dark" style="left:423px;top:265px">
    <div class="photo" style="background:linear-gradient(180deg,#d3c5ad,#b8935f 55%,#7c6a4c)" role="img" aria-label="Orange excavators working on a wide earthworks site"></div>
    <h3>Project Name Here</h3>
    <p>Lorem ipsum dolor sit amet, consectetur adipiscing elit, sed do eiusmod tempor incididunt ut labore et dolore magna aliqua. Vulputate dignissim suspendisse in est ante.</p>
  </div>
  <div class="project" style="left:795px;top:265px">
    <div class="photo" style="background:linear-gradient(180deg,#4d86c4,#c9b89b 60%,#8b7556)" role="img" aria-label="Backhoe loader moving a pile of sand"></div>
    <h3>Project Name Here</h3>
    <p>Lorem ipsum dolor sit amet, consectetur adipiscing elit, sed do eiusmod tempor incididunt ut labore et dolore magna aliqua. Vulputate dignissim suspendisse in est ante.</p>
  </div>
</section>

<div class="excavator" style="left:-20px;background:linear-gradient(200deg,#e3a728,#9c6a14 70%,rgba(60,40,10,0))" role="img" aria-label="Yellow excavator arm reaching in from the left"></div>
<div class="excavator" style="left:800px;background:linear-gradient(160deg,#e3a728,#9c6a14 70%,rgba(60,40,10,0))" role="img" aria-label="Yellow excavator arm reaching in from the right"></div>
<h2 class="abs" style="top:2131px;width:1200px;text-align:center;color:#fff;font-size:44px">Fast, Reliable<br>Excavation Services<br>Across Perth, WA.</h2>
<span class="btn abs" style="left:515px;top:2281px">Get a free quote <svg viewBox="0 0 16 16"><circle cx="8" cy="8" r="7" fill="none" stroke="#111" stroke-width="1.6"/><path d="M5 8h6M8.5 5.5 11 8l-2.5 2.5" fill="none" stroke="#111" stroke-width="1.6"/></svg></span>

<section class="quote">
  <h2>Get a Free Quote Today</h2>
  <p class="lead">Looking for dependable earthworks or excavation services in Perth, WA?<br><b>Contact Bluegum Ridge Earthworks today</b> for a free, no-obligation quote and expert advice on your next project.</p>
  <div class="abs" style="left:65px;top:283px;width:516px;height:266px;border-radius:14px;background:linear-gradient(180deg,#3c4a5c,#c0652a 45%,#f0a53c 60%,#3a2a1e)" role="img" aria-label="Excavator at sunset beside a site engineer in hi-vis holding plans"></div>
  <div class="abs" style="left:425px;top:218px;width:110px;height:340px;border-radius:40px 40px 10px 10px;background:linear-gradient(180deg,#e6e6e6,#d8e300 35%,#1d2a44 65%)" role="img" aria-label="Site engineer in hard hat and hi-vis vest"></div>
  <div class="form">
    <label style="left:22px;top:20px">Name</label>
    <label style="left:272px;top:20px">Email</label>
    <div class="field" style="left:22px;top:42px;width:242px">Name</div>
    <div class="field" style="left:272px;top:42px;width:242px">Email</div>
    <label style="left:22px;top:83px">Phone</label>
    <label style="left:272px;top:83px">Subject</label>
    <div class="field" style="left:22px;top:106px;width:242px">Phone</div>
    <div class="field" style="left:272px;top:106px;width:242px">Subject</div>
    <label style="left:22px;top:155px">Message</label>
    <div class="field" style="left:22px;top:178px;width:492px;height:80px">Message</div>
    <div class="send">Send your message</div>
  </div>
</section>

<footer class="site-footer">
  <div class="abs" style="inset:0;opacity:.5;background:radial-gradient(ellipse at 60% 40%,#4a3b28,transparent 70%)" role="img" aria-label="Dark background of earthmoving machinery"></div>
  <div class="foot-brand"><i></i>Bluegum Ridge Earthworks</div>
  <p class="foot-about">Bluegum Ridge Earthworks offers a full range of excavation and earthworks services throughout Perth and Western Australia.</p>
  <div class="social"><span></span><span></span><span></span></div>
  <div class="col" style="left:333px"><h4>Our Company</h4><ul><li>Home</li><li>About Us</li><li>Projects</li><li>Contact Us</li></ul></div>
  <div class="col" style="left:612px"><h4>Our Services</h4><ul><li>Excavation Services</li><li>Site Preparation &amp; Levelling</li><li>Land Clearing &amp; Earthmoving</li><li>Trenching &amp; Footings</li></ul></div>
  <div class="col contact" style="left:891px;width:270px"><h4>Get In Touch</h4><ul>
    <li><svg viewBox="0 0 12 12"><path d="M6 11S2 7 2 4.5a4 4 0 0 1 8 0C10 7 6 11 6 11z" fill="#cddc00"/><circle cx="6" cy="4.5" r="1.4" fill="#222"/></svg>14 Quarry Lane, Kelmscott WA 6111, Australia</li>
    <li><svg viewBox="0 0 12 12"><path d="M3 1l2 3-1 1.5c.8 1.5 2 2.7 3.5 3.5L9 8l3 2-1.5 2C6 11.5.5 6 0 1.5z" fill="#cddc00"/></svg>+61 400 128 356</li>
    <li><svg viewBox="0 0 12 12"><rect x="1" y="3" width="10" height="7" fill="#cddc00"/><path d="M1 3l5 4 5-4" fill="none" stroke="#222"/></svg>support@bluegumridge.com.au</li>
  </ul></div>
  <p class="copyright">Copyright © 2026 Bluegum Ridge Earthworks | Powered By Bluegum Ridge Earthworks</p>
</footer>

</body>
</html>
```